Business Card for a New Zealand IT Startup

I need a business card for VELTA Holdings. We are a young startup based in New Zealand working in internet marketing and web development. The design should have some element connected to New Zealand, such as wave, koru or silver fern, just don't use a kiwi bird.

```html
<!DOCTYPE html>
<html lang="en">
<head>
<meta charset="UTF-8">
<title>VELTA Holdings – Business Card</title>
<link rel="stylesheet" href="https://fonts.googleapis.com/css2?family=Montserrat:wght@700&family=Open+Sans:wght@400;600;700&display=swap">
<style>
  :root {
    --blue: #0a6ab4;
    --orange: #ea5a22;
    --orange-dark: #c94a1a;
    --ink: #3a3a3a;
    --paper: #ffffff;
    --backdrop: #e6e7e9;
  }
  * { margin: 0; padding: 0; box-sizing: border-box; }
  html, body {
    width: 1200px; height: 1000px; overflow: hidden;
    background: var(--backdrop);
    font-family: "Open Sans", Arial, sans-serif;
  }
  .card {
    position: absolute;
    left: 320px;
    width: 560px; height: 320px;
    background: var(--paper);
    box-shadow: 0 6px 18px rgba(0,0,0,.12);
    overflow: hidden;
  }
  .card--front { top: 130px; }
  .card--back  { top: 550px; }

  /* Front */
  .brand {
    position: absolute; inset: 0;
    display: flex; align-items: center; justify-content: center; gap: 14px;
  }
  .brand__mark { width: 22px; height: 22px; background: var(--orange); }
  .brand__name {
    font-family: "Montserrat", Arial, sans-serif;
    font-weight: 700; font-size: 46px; letter-spacing: 1px;
    color: var(--blue);
  }

  /* Back */
  .identity { position: absolute; left: 0; top: 26px; }
  .identity__bar {
    position: absolute; left: 0; top: 0;
    width: 14px; height: 38px; background: var(--blue);
  }
  .identity__name {
    margin-left: 34px;
    font-weight: 700; font-size: 19px; color: var(--blue); line-height: 1.1;
  }
  .identity__role {
    margin-left: 34px;
    font-weight: 600; font-size: 14px; color: var(--orange); letter-spacing: .5px;
  }
  .contact {
    position: absolute; left: 34px; top: 140px;
    font-size: 15px; color: var(--ink); line-height: 21px;
    list-style: none;
  }
  .contact__address { margin-bottom: 2px; }
  .contact__item { display: flex; align-items: center; gap: 7px; }
  .contact__icon { width: 14px; height: 14px; fill: var(--blue); flex: none; }
  .accent { position: absolute; right: 0; top: 0; width: 560px; height: 320px; }
</style>
</head>
<body>

<section class="card card--front" aria-label="Card front">
  <div class="brand">
    <span class="brand__mark"></span>
    <span class="brand__name">VELTA Holdings</span>
  </div>
</section>

<section class="card card--back" aria-label="Card back">
  <svg class="accent" viewBox="0 0 560 320" aria-hidden="true">
    <path d="M420 0 L560 0 L560 320 L470 320 C540 240 530 90 420 0 Z" fill="var(--orange)"/>
    <circle cx="410" cy="190" r="82" fill="var(--blue)"/>
  </svg>

  <header class="identity">
    <span class="identity__bar"></span>
    <p class="identity__name">MARA TANE</p>
    <p class="identity__role">PRESIDENT</p>
  </header>

  <ul class="contact">
    <li class="contact__address">27 Harbourview Road<br>Wellington 6011, NZ</li>
    <li class="contact__item">
      <svg class="contact__icon" viewBox="0 0 16 16"><path d="M2 5c0-2 2-3 6-3s6 1 6 3v1h-3V5H5v1H2zM4 7h8l2 6H2z"/></svg>
      021 4830 7715
    </li>
    <li class="contact__item">
      <svg class="contact__icon" viewBox="0 0 16 16"><path d="M4 1h8v14H4zM5.5 3v9h5V3z"/></svg>
      022 6194 2087
    </li>
    <li class="contact__item">
      <svg class="contact__icon" viewBox="0 0 16 16"><path d="M4 1h8v4H4zM1 6h14v7H1zM4 11h8v4H4z"/></svg>
      04 3918 6420
    </li>
    <li class="contact__item">
      <svg class="contact__icon" viewBox="0 0 16 16"><path d="M1 3h14v1L8 9 1 4zM1 6l7 5 7-5v7H1z"/></svg>
      mara@veltaholdings.com
    </li>
    <li class="contact__item">
      <svg class="contact__icon" viewBox="0 0 16 16"><circle cx="8" cy="8" r="7"/></svg>
      www.veltaholdings.com
    </li>
  </ul>
</section>

</body>
</html>
```